Mobile Friendly Lead Generation Landing Page

We are a web marketing company that specialized in web lead generation. Recently we have started buying media from mobile devices and we need a mobile interface(landing page) where we can collect user data in an effective manner.

Our current mobile landing page is:
http://www.tutorpath.example.com/lp13d/index.aspx?a=true&source=841356
Through this you can see what the steps/questions users need to answer to get matched to a school. We need the design for the whole process.

We are pretty open for design ideas and our goal is to make this mobile optimized landing page have the look and feel of an app...but not an app.
There are several questions in the process but we are open to changing the way they are presented. As in, you can have one question at a time or a few.
The goal is to make this EXTREMELY EASY for users to interact with.

One example that we have liked is:
http://learnvane.example/schools/57214-page1.lvne (please note that this opens only on mobile devices)

Some of these screenshots are attached.

Our web form looks like this:
http://www.tutorpath.example.com/lp88/index.aspx?a=true

```html
<!DOCTYPE html>
<html lang="en">
<head>
<meta charset="utf-8">
<title>TutorPath – Area of Study</title>
<link rel="stylesheet" href="https://fonts.googleapis.com/css2?family=Roboto:wght@300;400;500&family=Libre+Baskerville:wght@700&display=swap">
<style>
  :root {
    --page-bg: #ffffff;
    --brand-band: #f6f3e8;
    --ink-dark: #111111;
    --ink-mid: #5f5f5f;
    --ink-soft: #6a6a6a;
    --accent: #1b97e6;
    --accent-deep: #0f86d6;
    --track: #e3e6ea;
    --track-mid: #d2d8de;
    --row-top: #fbfbfb;
    --row-bottom: #e8e8e8;
    --row-line: #d6d6d6;
    --icon-ring: #cfcfcf;
    --icon-fill: #e7e7e7;
    --icon-ink: #a4a4a4;
    --chevron: #c4c4c4;
  }
  * { box-sizing: border-box; margin: 0; padding: 0; }
  html, body {
    width: 1200px; height: 2773px; overflow: hidden;
    background: var(--page-bg);
    font-family: "Roboto", "Helvetica Neue", Arial, sans-serif;
  }
  .landing { width: 1200px; height: 2773px; position: relative; }

  .brand-band {
    height: 146px; background: var(--brand-band);
    display: flex; align-items: center; justify-content: center; gap: 18px;
  }
  .brand-mark { width: 34px; height: 34px; border-radius: 50%; background: #b9c24a; }
  .brand-name {
    font-family: "Libre Baskerville", Georgia, serif; font-weight: 700;
    font-size: 46px; color: var(--ink-dark); letter-spacing: -0.5px;
  }

  .hero {
    position: relative; height: 451px; overflow: hidden;
    background: radial-gradient(ellipse at 68% 45%, #e6cdb3 0%, #efe2d2 30%, #f3ede4 55%, #f4f1ea 80%);
  }
  .hero-visual { position: absolute; inset: 0; }
  .hero-copy { position: absolute; left: 40px; top: 78px; }
  .hero-line { display: block; line-height: 1.08; }
  .hero-line--lead { font-size: 84px; font-weight: 400; color: var(--ink-dark); letter-spacing: -2px; }
  .hero-line--main { font-size: 98px; font-weight: 300; color: var(--ink-mid); letter-spacing: -2.5px; }
  .hero-line--cta { font-size: 98px; font-weight: 300; color: var(--accent); letter-spacing: -2px; }

  .progress {
    position: absolute; left: 22px; top: 691px; width: 1159px; height: 29px;
    border-radius: 15px; background: var(--track); overflow: hidden;
  }
  .progress-next { position: absolute; left: 0; top: 0; height: 100%; width: 334px; background: var(--track-mid); }
  .progress-done {
    position: absolute; left: 0; top: 0; height: 100%; width: 199px;
    border-radius: 15px; background: linear-gradient(#3fb0f2, var(--accent-deep));
  }

  .question {
    position: absolute; left: 22px; top: 800px;
    font-size: 53px; font-weight: 400; color: var(--ink-mid);
  }

  .study-list { position: absolute; left: 0; top: 918px; width: 1200px; list-style: none; }
  .study-option {
    position: relative; height: 157px; display: flex; align-items: center;
    background: linear-gradient(var(--row-top), var(--row-bottom));
    border-bottom: 2px solid #f7f7f7;
    color: var(--ink-soft);
  }
  .study-option--active { background: var(--accent); color: #fff; border-bottom-color: var(--accent); }
  .option-icon {
    position: absolute; left: 37px; width: 102px; height: 102px; border-radius: 50%;
    border: 3px solid var(--icon-ring); background: var(--icon-fill);
    display: flex; align-items: center; justify-content: center;
  }
  .study-option--active .option-icon { border-color: #fff; background: transparent; }
  .option-icon svg { width: 52px; height: 52px; fill: var(--icon-ink); stroke: none; }
  .study-option--active .option-icon svg { fill: #fff; }
  .option-label { position: absolute; left: 190px; font-size: 48px; font-weight: 400; }
  .option-go {
    position: absolute; left: 1071px; top: 0; width: 129px; height: 100%;
    border-left: 2px solid var(--row-line);
    display: flex; align-items: center; justify-content: center;
  }
  .study-option--active .option-go { border-left-color: #0c7cc6; }
  .option-go svg { width: 26px; height: 40px; fill: none; stroke: var(--chevron); stroke-width: 6; stroke-linecap: round; stroke-linejoin: round; }
  .study-option--active .option-go svg { stroke: #fff; }
</style>
</head>
<body>
<main class="landing">
  <header class="brand-band">
    <span class="brand-mark"></span>
    <span class="brand-name">TutorPath</span>
  </header>

  <section class="hero">
    <div class="hero-visual" role="img" aria-label="Soft-focus photo of a student studying outdoors"></div>
    <h1 class="hero-copy">
      <span class="hero-line hero-line--lead">GET MATCHED TO</span>
      <span class="hero-line hero-line--main">Online &amp; Local Colleges</span>
      <span class="hero-line hero-line--cta">Now!</span>
    </h1>
  </section>

  <div class="progress" aria-label="Step 1 of the matching form">
    <span class="progress-next"></span>
    <span class="progress-done"></span>
  </div>

  <p class="question">Please select your Area of Study:</p>

  <ul class="study-list">
    <li class="study-option study-option--active">
      <span class="option-icon"><svg viewBox="0 0 24 24"><path d="M5 2h14v20H5z M7 4v4h10V4z M7 10h2v2H7z M11 10h2v2h-2z M15 10h2v2h-2z M7 14h2v2H7z M11 14h2v2h-2z M15 14h2v6h-2z M7 18h2v2H7z M11 18h2v2h-2z" fill-rule="evenodd"/></svg></span>
      <span class="option-label">Accounting</span>
      <span class="option-go"><svg viewBox="0 0 26 40"><path d="M6 6l14 14L6 34"/></svg></span>
    </li>
    <li class="study-option">
      <span class="option-icon"><svg viewBox="0 0 24 24"><circle cx="10" cy="7" r="4.5"/><path d="M2 22c0-5 3.5-8 8-8 1.5 0 2.8.3 3.9.9L14 22z"/><circle cx="18.5" cy="18" r="3.5"/></svg></span>
      <span class="option-label">Business Administration</span>
      <span class="option-go"><svg viewBox="0 0 26 40"><path d="M6 6l14 14L6 34"/></svg></span>
    </li>
    <li class="study-option">
      <span class="option-icon"><svg viewBox="0 0 24 24"><path d="M12 2l10 5v2H2V7z M4 10h3v8H4z M10.5 10h3v8h-3z M17 10h3v8h-3z M2 19h20v3H2z"/></svg></span>
      <span class="option-label">Business Management</span>
      <span class="option-go"><svg viewBox="0 0 26 40"><path d="M6 6l14 14L6 34"/></svg></span>
    </li>
    <li class="study-option">
      <span class="option-icon"><svg viewBox="0 0 24 24"><circle cx="7" cy="8" r="3"/><circle cx="17" cy="8" r="3"/><circle cx="12" cy="10" r="3.3"/><path d="M1 18c0-3 2.5-5 6-5s6 2 6 5z M11 18c0-3 2.5-5 6-5s6 2 6 5z M5.5 21c0-3.5 3-5.5 6.5-5.5s6.5 2 6.5 5.5z"/></svg></span>
      <span class="option-label">Comunication</span>
      <span class="option-go"><svg viewBox="0 0 26 40"><path d="M6 6l14 14L6 34"/></svg></span>
    </li>
    <li class="study-option">
      <span class="option-icon"><svg viewBox="0 0 24 24"><path d="M3 15h4v7H3z M10 11h4v11h-4z M17 6h4v16h-4z M3 11l6-5 4 3 7-7 1 1-8 8-4-3-5 4z"/></svg></span>
      <span class="option-label">E Business</span>
      <span class="option-go"><svg viewBox="0 0 26 40"><path d="M6 6l14 14L6 34"/></svg></span>
    </li>
  </ul>
</main>
</body>
</html>
```